Automotive Accessories Business Card

Design a business template that match our new logo design and our industry.

https://www.qelmotorgear.com/

Target Market(s)

Aftermarket auto parts and accessories

Industry/Entity Type

automotive

Contact Information for Business Card

company logo

Font styles to use
Serif
Sans Serif

Colors
EB3D1F
EC4F4E
F09395
F8D3D4
FCEDEE

```html
<!DOCTYPE html>
<html lang="en">
<head>
<meta charset="UTF-8">
<title>QEL Motor Gear – Business Card</title>
<link href="https://fonts.googleapis.com/css2?family=Montserrat:wght@400;500;700;800&display=swap" rel="stylesheet">
<style>
  :root {
    --red: #d4202a;
    --red-dark: #8e0d12;
    --red-light: #ec4f4e;
    --ink: #3b3b3d;
    --paper: #ffffff;
    --backdrop: #e6e6e8;
    --rule: #5a5a5a;
  }
  * { box-sizing: border-box; margin: 0; padding: 0; }
  html, body {
    width: 1200px; height: 802px; overflow: hidden;
    background: var(--backdrop);
    font-family: "Montserrat", Arial, sans-serif;
  }
  .stage {
    width: 1200px; height: 802px;
    display: flex; align-items: center; justify-content: center; gap: 40px;
  }
  .card {
    width: 500px; height: 286px; position: relative; overflow: hidden;
    box-shadow: 0 10px 24px rgba(0,0,0,.18);
  }
  /* front */
  .card--front { background: var(--paper); border-bottom: 3px solid var(--red); }
  .brand {
    position: absolute; top: 42px; right: 44px;
    display: flex; align-items: center; gap: 10px;
  }
  .brand__mark { width: 18px; height: 18px; background: var(--red); }
  .brand__name {
    font-weight: 800; font-size: 26px; letter-spacing: 1px;
    color: var(--ink); text-transform: uppercase; line-height: 1;
  }
  .divider {
    position: absolute; left: 36px; right: 36px; top: 140px;
    height: 1px; background: var(--rule);
  }
  .person { position: absolute; left: 40px; top: 160px; }
  .person__name {
    font-weight: 800; font-size: 17px; letter-spacing: 2px;
    color: var(--red); text-transform: uppercase;
  }
  .person__title { font-size: 12px; color: var(--ink); margin-top: 3px; }
  .contacts { list-style: none; margin-top: 14px; }
  .contacts li {
    display: flex; align-items: center; gap: 8px;
    font-size: 11.5px; color: var(--ink); margin-bottom: 4px;
  }
  .contacts svg { width: 10px; height: 10px; fill: var(--red); flex: none; }
  .address {
    position: absolute; right: 40px; top: 160px; text-align: right;
    font-size: 11.5px; line-height: 1.55; color: var(--ink); font-style: normal;
  }
  /* back */
  .card--back {
    background: radial-gradient(ellipse at 80% 20%, var(--red-light) 0%, var(--red) 45%, var(--red-dark) 100%);
    display: flex; align-items: center; justify-content: center;
  }
  .back__brand { display: flex; align-items: center; gap: 14px; }
  .back__mark { width: 26px; height: 26px; background: #fff; }
  .back__name {
    color: #fff; font-weight: 800; font-size: 30px;
    letter-spacing: 1.5px; text-transform: uppercase;
  }
</style>
</head>
<body>
<main class="stage">
  <section class="card card--front">
    <div class="brand">
      <span class="brand__mark"></span>
      <span class="brand__name">QEL Motor Gear Inc</span>
    </div>
    <div class="divider"></div>
    <div class="person">
      <h1 class="person__name">Daniel Reyes</h1>
      <p class="person__title">Manager</p>
      <ul class="contacts">
        <li><svg viewBox="0 0 10 10"><path d="M2 0h2l1 3-1.5 1a6 6 0 0 0 2.5 2.5L7 5l3 1v2a2 2 0 0 1-2 2A8 8 0 0 1 0 2a2 2 0 0 1 2-2z"/></svg>1-866-555-0142</li>
        <li><svg viewBox="0 0 10 10"><path d="M0 2h10v6H0zM0 2l5 3.5L10 2" stroke="#fff" stroke-width=".8"/></svg>sales@qelmotorgear.com</li>
        <li><svg viewBox="0 0 10 10"><circle cx="5" cy="5" r="5"/></svg>www.qelmotorgear.com</li>
      </ul>
    </div>
    <address class="address">218 N. Oak St.<br>Unit C<br>Riverton, CA 91700</address>
  </section>

  <section class="card card--back">
    <div class="back__brand">
      <span class="back__mark"></span>
      <span class="back__name">QEL Motor Gear Inc</span>
    </div>
  </section>
</main>
</body>
</html>
```